Start-Up für Training, Coaching & Consulting sucht modernes Webdesign!
Zielgruppe
Wer ist TAVI Training, Coaching & Consulting?
Wir führen Führungskräftetrainings durch, machen Privatkunden für Bewerbungen fit und unterstützen Unternehmen mit Verkaufstrainings. Wir entwickeln Persönlichkeiten im Coaching. Wir beraten Unternehmen und helfen ihnen dabei, ihre Geschäftsabläufe und Prozesse zu optimieren. Dabei steht unsere hohe Qualität im Mittelpunkt - gemeinsam mit unseren kreativen Trainingsmethoden. Unser Background (Diplom-Kaufleute und geprüfte Trainer) bietet dafür die passende Ausgangslage.
Was bedeutet TAVI?
Tavi ist Maori und bdeutet Kreis/Spirale. Er symbolisiert einen wachsenden Silberfarn und steht für persönliche Entwicklung und Entfaltung. Der Tavi ist einerseits unser Namensgeber und unser Logo, andererseits steht der Tavi aber auch für unsere Werte: Denn wir wollen unseren Kunden dabei helfen zu wachsen und sich weiterzuentwickeln - und dies auf eine hochqualitative und seriöse Art und Weise ohne den Eindruck von Esoterik oder Erlebnispädagogik zu vermitteln.
Aufgabenstellung
Modernes Design, das unsere Philosophie widerspiegelt: Wir möchten unseren Kunden auf seriöse und hochqualitative Weise weiterentwickeln. Wir stehen für nachhaltigen Lernerfolg, kreative Trainingsmethoden, Abwechslung, Spaß am Lernen, Qualität, Kompetenz, Fachwissen und Dynamik.
Layout:
1) Header: QMSR geprüfter Trainer, Menüpunkte (siehe Architektur)
2) Banner
3) 3 Teaser (Training, Coaching, Consulting) + Header + 2-3 Zeilen Text (+Icons)
>>> Sichtbarer Bereich auf Homepage: Menü, Banner, Teaser
4) "Warum Sie uns wählen sollten": 5 bullet points ohne weiteren Text
5) "Aus unserem Blog": Frame für 3 Blogartikel + Bild + Datum + Header + 2-3 Zeilen Text
6) Alle drei QMSR Logos
7) Footer: Click Us (quick links), Contact Us (Adresse), Follow Us (Pinnwald, ZOLP, Kontaktor)
8) Copyright + Impressum
>>> Das Design soll klar sein, aber nicht zu kantig. Vielmehr sollen abgerundete Ecken und dynamische Elemente genutzt werden.
Architektur:
3 Ebenen:
1) Homepage
2) TAVI, Training, Coaching, Consulting, für Trainer, Kundenstimmen/Referenzen, Kontakt
3) noch zu bestimmende Produktdetailseiten
Texte werden noch erstellt, Layout kann ggf. mit Platzhaltertext gefüllt werden.
Bildmaterial: Logo und vorhandenes Imagebild werden zur Verfügung gestellt. Bilder können ggf. gekauft werden. Vorschläge erwünscht.
Corporate colors:
grün: #a2c61b + monochromatic colors
http://www.tintoskop.de/a2c61b
grau: #474747 + monochromatic colors
http://www.tintoskop.de/474747

```html
<!DOCTYPE html>
<html lang="de">
<head>
<meta charset="utf-8">
<title>TAVI Training, Coaching &amp; Consulting</title>
<link href="https://fonts.googleapis.com/css2?family=Ubuntu:wght@400;500;700&display=swap" rel="stylesheet">
<style>
:root{
  --green:#a2c61b;
  --green-light:#b5d33a;
  --green-pale:#c9df6a;
  --grey:#474747;
  --grey-dark:#2a2a2a;
  --text:#222;
  --white:#fff;
  --blue:#0f5fae;
}
*{margin:0;padding:0;box-sizing:border-box}
html,body{width:849px;height:1200px;overflow:hidden;background:var(--white)}
body{position:relative;font-family:'Ubuntu',sans-serif;color:var(--text)}
.abs{position:absolute}

/* header */
.site-header{position:absolute;left:0;top:0;width:849px;height:56px;background:var(--white)}
.brand{position:absolute;left:44px;top:10px}
.brand-name{font-size:27px;font-weight:700;color:var(--grey);letter-spacing:1px;line-height:28px}
.brand-tag{font-size:5px;color:var(--grey);margin-top:4px;border-top:1px solid var(--green);padding-top:2px;width:78px}
.cert-badge{position:absolute;left:193px;top:17px;width:81px;height:22px;background:var(--blue)}
.main-nav{position:absolute;top:22px;left:0;width:849px;font-size:11.5px;font-weight:500;color:var(--grey-dark)}
.main-nav span{position:absolute;white-space:nowrap}
.main-nav .active{color:var(--green)}
.header-rule{position:absolute;left:0;top:56px;width:849px;height:6px;background:linear-gradient(90deg,var(--green-pale),var(--green))}

/* hero */
.hero{position:absolute;left:0;top:62px;width:849px;height:324px;
  background:radial-gradient(ellipse at 60% 40%,#6fb53a 0%,#3b8a22 35%,#1d4f12 75%,#0f2a09 100%)}
.hero-title{position:absolute;left:132px;top:139px;font-size:19px;line-height:22.5px;color:var(--white)}
.hero-btn{position:absolute;left:133px;top:213px;width:89px;height:29px;border-radius:15px;background:var(--green-light);
  font-size:7px;font-weight:700;color:var(--grey-dark);display:flex;align-items:center;justify-content:center}
.hero-arrow{position:absolute;top:160px;width:32px;height:32px}

/* teasers */
.band-rule{position:absolute;left:0;top:334px;width:849px;height:5px;background:linear-gradient(90deg,var(--green-pale),var(--green))}
.teaser{position:absolute;top:288px;width:227px;height:400px;background:var(--white);border-radius:21px 21px 0 0;
  box-shadow:0 0 8px rgba(0,0,0,.12);
  -webkit-mask-image:linear-gradient(#000 70%,transparent);mask-image:linear-gradient(#000 70%,transparent)}
.teaser-icon{position:absolute;top:311px;width:50px;height:50px;border-radius:50%;background:var(--green-light);
  border:3px solid var(--white);box-shadow:0 2px 5px rgba(0,0,0,.25)}
.teaser-title{position:absolute;top:374px;width:227px;text-align:center;font-size:12.5px;font-weight:500;color:var(--green)}
.teaser-img{position:absolute;top:405px;width:181px;height:92px;border-radius:6px 6px 0 0}
.teaser-text{position:absolute;top:510px;width:180px;font-size:8.4px;line-height:13.6px;color:var(--grey-dark)}
.more{color:var(--green);font-weight:500}
.more i{display:inline-block;width:6px;height:6px;border-radius:50%;background:var(--green);margin-left:5px;vertical-align:middle}

/* reasons */
.section-title{position:absolute;top:639px;font-size:19px;font-weight:500;color:var(--grey-dark)}
.reason{position:absolute;left:108px;font-size:15.7px;color:var(--green-light);display:flex;align-items:center}
.reason svg{margin-right:17px}

/* blog */
.blog-img{position:absolute;left:463px;width:94px;height:77px;border-radius:4px}
.blog-item{position:absolute;left:585px;width:180px}
.blog-date{font-size:7.5px;color:var(--grey-dark)}
.blog-head{font-size:12.5px;color:var(--green-light);margin-top:2px}
.blog-text{font-size:7.3px;line-height:10.5px;color:#666}
.blog-item .more{font-size:7.3px}

/* partner badges */
.partner{position:absolute;top:1014px;height:24px;background:var(--blue)}

/* footer */
.footer-rule{position:absolute;left:0;top:1079px;width:849px;height:6px;background:linear-gradient(90deg,var(--green-pale),var(--green))}
.site-footer{position:absolute;left:0;top:1085px;width:849px;height:115px;background:var(--grey-dark);color:var(--white)}
.footer-brand{position:absolute;left:89px;top:22px}
.footer-brand .brand-name{color:var(--white)}
.footer-brand .brand-tag{color:#ccc}
.footer-col{position:absolute;top:22px;font-size:9.4px;line-height:12.4px;font-weight:500}
.footer-col h3{font-size:12.5px;font-weight:500;color:var(--green-light);margin-bottom:6px}
.social-dot{display:inline-block;width:7px;height:7px;border-radius:50%;background:var(--white);margin-right:8px;vertical-align:-1px}
</style>
</head>
<body>

<header class="site-header">
  <div class="brand">
    <div class="brand-name">TAVI</div>
    <div class="brand-tag">Training • Coaching • Consulting</div>
  </div>
  <div class="cert-badge" role="img" aria-label="Zertifikat geprüfter Business-Trainer"></div>
  <nav class="main-nav">
    <span class="active" style="left:367px">LEISTUNGEN ▾</span>
    <span style="left:473px">ÜBER UNS</span>
    <span style="left:556px">FÜR TRAINER ⌄</span>
    <span style="left:666px">REFERENZEN</span>
    <span style="left:766px">KONTAKT</span>
  </nav>
</header>
<div class="header-rule"></div>

<section class="hero" role="img" aria-label="Farnspirale in grünem Wald"></section>
<h1 class="hero-title" style="font-weight:400">Lernen und Wissen<br>vermitteln:<br>Leicht gemacht</h1>
<div class="hero-btn">MEHR ERFAHREN</div>
<svg class="hero-arrow" style="left:44px" viewBox="0 0 32 32"><circle cx="16" cy="16" r="16" fill="#a2c61b"/><path d="M18 9l-7 7 7 7" stroke="#222" stroke-width="3.5" fill="none" stroke-linecap="round"/></svg>
<svg class="hero-arrow" style="left:772px" viewBox="0 0 32 32"><circle cx="16" cy="16" r="16" fill="#a2c61b"/><path d="M14 9l7 7-7 7" stroke="#222" stroke-width="3.5" fill="none" stroke-linecap="round"/></svg>

<div class="band-rule"></div>

<div class="teaser" style="left:44px"></div>
<div class="teaser" style="left:311px"></div>
<div class="teaser" style="left:577px"></div>

<div class="teaser-icon" style="left:134px"></div>
<div class="teaser-icon" style="left:399px"></div>
<div class="teaser-icon" style="left:666px"></div>

<h2 class="teaser-title" style="left:46px">TRAINING</h2>
<h2 class="teaser-title" style="left:311px">COACHING</h2>
<h2 class="teaser-title" style="left:577px">CONSULTING</h2>

<div class="teaser-img" style="left:67px;background:linear-gradient(#6b8fb8,#e6b56a 60%,#5c5a3a)" role="img" aria-label="Läufer auf Bergstraße im Sonnenuntergang"></div>
<div class="teaser-img" style="left:333px;background:radial-gradient(circle at 50% 60%,#6cbf3c,#2d6e1a)" role="img" aria-label="Farnspirale"></div>
<div class="teaser-img" style="left:599px;background:linear-gradient(#cfd2d4,#8d9196 60%,#2e2e2e)" role="img" aria-label="Person auf Felsvorsprung im Gebirge"></div>

<p class="teaser-text" style="left:68px">Durch mich gebiert das Netz die Kunst aus sich selbst heraus. Nicht schlicht reproduk-tiver Natur, repräsentiere ich vielmehr die kontinuierliche Evolution des Wortes.<br><span class="more">mehr<i></i></span></p>
<p class="teaser-text" style="left:334px">Durch mich gebiert das Netz die Kunst aus sich selbst heraus. Nicht schlicht reproduk-tiver Natur, repräsentiere ich vielmehr die kontinuierliche Evolution des Wortes.<br><span class="more">mehr<i></i></span></p>
<p class="teaser-text" style="left:602px">Durch mich gebiert das Netz die Kunst aus sich selbst heraus. Nicht schlicht reproduk-tiver Natur, repräsentiere ich vielmehr die kontinuierliche Evolution des Wortes.<br><span class="more">mehr<i></i></span></p>

<h2 class="section-title" style="left:101px">Warum Sie uns wählen sollten</h2>
<div class="reason" style="top:688px"><svg width="19" height="19" viewBox="0 0 20 20"><circle cx="10" cy="10" r="10" fill="#a2c61b"/><path d="M8 5l5 5-5 5" stroke="#222" stroke-width="2.5" fill="none"/></svg>Grund Nummer Eins</div>
<div class="reason" style="top:749px"><svg width="19" height="19" viewBox="0 0 20 20"><circle cx="10" cy="10" r="10" fill="#a2c61b"/><path d="M8 5l5 5-5 5" stroke="#222" stroke-width="2.5" fill="none"/></svg>Grund Nummer Zwei</div>
<div class="reason" style="top:811px"><svg width="19" height="19" viewBox="0 0 20 20"><circle cx="10" cy="10" r="10" fill="#a2c61b"/><path d="M8 5l5 5-5 5" stroke="#222" stroke-width="2.5" fill="none"/></svg>Grund Nummer Drei</div>
<div class="reason" style="top:875px"><svg width="19" height="19" viewBox="0 0 20 20"><circle cx="10" cy="10" r="10" fill="#a2c61b"/><path d="M8 5l5 5-5 5" stroke="#222" stroke-width="2.5" fill="none"/></svg>Grund Nummer Vier</div>
<div class="reason" style="top:937px"><svg width="19" height="19" viewBox="0 0 20 20"><circle cx="10" cy="10" r="10" fill="#a2c61b"/><path d="M8 5l5 5-5 5" stroke="#222" stroke-width="2.5" fill="none"/></svg>Grund Nummer Fünf</div>

<h2 class="section-title" style="left:586px">Aus unserem Blog</h2>

<div class="blog-img" style="top:683px;background:linear-gradient(135deg,#8a6a48,#3a3a3a)" role="img" aria-label="Person am Laptop"></div>
<div class="blog-item" style="top:682px">
  <div class="blog-date">02.02.2016</div>
  <div class="blog-head">Heading 01</div>
  <p class="blog-text">Durch mich gebiert das Netz die Kunst aus sich selbst heraus. Nicht schlicht reproduktiver Natur, repräsentiere ich vielmehr die kontinuierliche Evolution des Wortes.<br><span class="more">mehr<i></i></span></p>
</div>

<div class="blog-img" style="top:788px;background:linear-gradient(135deg,#5f8a94,#9cb3b0 60%,#4b5a55)" role="img" aria-label="Yoga auf einem Felsen am Wasser"></div>
<div class="blog-item" style="top:786px">
  <div class="blog-date">09.02.2016</div>
  <div class="blog-head">Heading 02</div>
  <p class="blog-text">Durch mich gebiert das Netz die Kunst aus sich selbst heraus. Nicht schlicht reproduktiver Natur, repräsentiere ich vielmehr die kontinuierliche Evolution des Wortes.<br><span class="more">mehr<i></i></span></p>
</div>

<div class="blog-img" style="top:889px;background:linear-gradient(135deg,#7a3a26,#b0703e 60%,#5a3420)" role="img" aria-label="Besprechung am Holztisch"></div>
<div class="blog-item" style="top:888px">
  <div class="blog-date">14.02.2016</div>
  <div class="blog-head">Heading 03</div>
  <p class="blog-text">Durch mich gebiert das Netz die Kunst aus sich selbst heraus. Nicht schlicht reproduktiver Natur, repräsentiere ich vielmehr die kontinuierliche Evolution des Wortes.<br><span class="more">mehr<i></i></span></p>
</div>

<div class="partner" style="left:316px;width:17px" role="img" aria-label="Mitgliedsabzeichen"></div>
<div class="partner" style="left:373px;width:17px" role="img" aria-label="Verbandsabzeichen"></div>
<div class="partner" style="left:443px;width:85px" role="img" aria-label="Zertifikat geprüfter Business-Trainer"></div>

<div class="footer-rule"></div>
<footer class="site-footer">
  <div class="footer-brand">
    <div class="brand-name">TAVI</div>
    <div class="brand-tag">Training • Coaching • Consulting</div>
  </div>
  <div class="footer-col" style="left:239px">
    <h3>Click Us</h3>
    Link Title Number 1<br>Link Title Number 2<br>Link Title Number 3
  </div>
  <div class="footer-col" style="left:398px">
    <h3>Contact Us</h3>
    Tavi GmbH<br>Musterstraße 22<br>78462 Musterstadt<br>Germany
  </div>
  <div class="footer-col" style="left:561px">
    <h3>Follow Us</h3>
    <span class="social-dot"></span>Pinnwald<br><span class="social-dot"></span>Zolp<br><span class="social-dot"></span>Kontaktor
  </div>
  <div class="footer-col" style="left:690px">
    <h3>Impressum</h3>
    © 2016 TAVI
  </div>
</footer>

</body>
</html>
```